Trevani.com- International Goal Achievement Coach Needs Website Design

I need a web design for my new company called Trevani. I help people who are stuck, people who have a big dream, but don't know how to get there. I help them to break their dreams down into small, manageable steps... and then I'm the "kick in the shin" to get them moving and thriving!

We can all be better- We can all DO better. I inspire people to Go Boldly in the direction of your dreams.

I have uploaded my logo along with some vintage champagne posters. Please use the vintage posters as inspiration. I like the bold, vintage look and feel. I would love the main colors of the design to be black, white and metallic gold. And to follow along this vintage look and feel. Please feel free to use the logo in black or metallic gold or white.

Target Market(s)

websites that I like- lunabrask.com & tessak.tv

I would like to also use the vintage champagne photos attached as inspiration as well.

Industry/Entity Type

It Company

Requirements
Must have
• Tabs should include: About, Work With Me, Praise, Giving Back

On the homepage add:
* Sign up for newsletter with space to enter name and email (No click throughs)
* Upcoming Events/Sessions
* Newsletter Posts
* Resources
* Praise Section

* Large photo on top with additional photos throughout the page/site.
Nice to have
• Any additions you can bring to the table would be greatly appreciated.

```html
<!DOCTYPE html>
<html lang="en">
<head>
<meta charset="utf-8">
<title>Trevani – International Goal Achievement Coach</title>
<link rel="stylesheet" href="https://fonts.googleapis.com/css2?family=Quicksand:wght@400;500;600;700&family=Kaushan+Script&display=swap">
<style>
:root{
  --brown-dark:#563618;
  --brown:#5b3a1b;
  --brown-tag:#7a5018;
  --gold:#f4c35a;
  --gold-soft:#c89a3a;
  --yellow:#ffd800;
  --heading:#c07a2a;
  --text:#4a4a4a;
  --muted:#8a8a8a;
  --panel:#ececec;
  --white:#ffffff;
  --footer:#4a4238;
  --green:#7ab81f;
}
*{margin:0;padding:0;box-sizing:border-box}
html,body{width:1200px;height:2922px;overflow:hidden;background:var(--white)}
body{position:relative;font-family:"Quicksand",sans-serif;color:var(--text)}
.abs{position:absolute}

/* header */
.site-header{left:0;top:0;width:1200px;height:120px;background:var(--brown)}
.brand{left:117px;top:21px;display:flex;align-items:center;gap:22px}
.brand-dot{width:78px;height:78px;border-radius:50%;background:#a67c4a}
.brand-name{font-size:38px;font-weight:600;color:var(--gold)}
.main-nav{left:436px;top:48px;display:flex;gap:33px;font-size:16px;font-weight:500;color:var(--gold)}

/* hero */
.hero{left:0;top:120px;width:1200px;height:500px;background:linear-gradient(100deg,#6b4a2c 0%,#a0764e 35%,#c89a70 55%,#8a6240 80%,#5a3e26 100%)}
.hero-title{left:189px;top:244px;width:460px;font-size:41px;font-weight:500;line-height:52px;color:var(--white)}
.hero-offer{left:189px;top:362px;font-size:30px;font-weight:600;color:var(--yellow)}
.field{top:425px;height:44px;background:var(--white);border-radius:3px;font-size:14px;color:#333;padding:13px 20px}
.field-name{left:191px;width:210px}
.field-mail{left:413px;width:210px}
.get-it{left:635px;top:399px;width:94px;height:94px;border-radius:50%;background:#4a2e14;color:var(--gold);font-family:"Kaushan Script",cursive;font-size:26px;display:flex;align-items:center;justify-content:center}
.slider-dots{left:116px;top:564px;display:flex;gap:5px}
.slider-dots span{width:14px;height:14px;border-radius:50%;background:var(--gold-soft)}
.slider-dots span.off{background:#3a2a1a}

/* posts */
.post-title{background:var(--brown-dark);color:var(--gold);font-size:22px;font-weight:500;line-height:32px;padding:0 20px;display:flex;align-items:center;white-space:nowrap;overflow:hidden}
.comments{background:var(--brown-tag);color:var(--white);font-size:15px;padding:8px 14px}
.photo{display:block}
.body-copy{font-size:13px;line-height:16.5px;color:var(--text);text-align:justify}
.body-copy p+p{margin-top:16px}
.share-label{font-size:16px;font-weight:500;color:var(--gold-soft)}
.share-row{display:flex;gap:9px}
.share-btn{background:#efefef;border:1px solid #e0e0e0;font-size:10px;color:#666;padding:5px 8px;text-transform:uppercase;display:flex;align-items:center;gap:4px}
.count{background:#3aa0d8;color:#fff;border-radius:6px;font-size:8px;padding:1px 4px}
.article-title{font-size:26px;font-weight:500;line-height:33px;color:var(--heading)}
.article-date{font-size:12px;color:var(--muted)}
.older{left:103px;top:2683px;width:118px;height:37px;background:#efefef;border-radius:3px;font-size:13px;color:#333;display:flex;align-items:center;justify-content:center;gap:8px}

/* sidebar */
.widget-head{background:#111;color:#ccc;font-size:14px;padding:10px 20px;height:40px}
.hot-events{left:736px;top:639px;width:328px;height:241px}
.hot-photo{width:328px;height:201px;background:linear-gradient(160deg,#1a2436 0%,#2a3a60 50%,#2c5a2a 100%);position:relative}
.hot-caption{position:absolute;left:20px;bottom:14px;color:var(--white)}
.hot-caption small{display:block;font-size:14px}
.hot-caption strong{font-size:29px;font-weight:500}
.side-label{font-size:15px;font-weight:500;color:#333}
.testimonial{left:736px;top:923px;width:328px;height:131px;background:var(--panel);font-size:12px;line-height:15px;padding:16px 16px;color:#555}
.testimonial-date{text-align:right;margin-top:10px;font-size:11px;color:#444}
.testimonial-tail{left:756px;top:1054px;width:0;height:0;border-left:26px solid var(--panel);border-bottom:16px solid transparent}
.resource{left:736px;width:328px;height:107px;color:var(--white);text-align:center;padding-top:27px}
.resource h3{font-size:27px;font-weight:500;line-height:30px}
.resource p{font-size:14px;letter-spacing:1px}
.r1{top:1116px;background:linear-gradient(90deg,#a8881a,#d4b420)}
.r2{top:1237px;background:linear-gradient(90deg,#8a4a20,#c07a40)}
.r3{top:1358px;background:#d8be5a}
.music{left:744px;top:1479px;width:300px;height:298px;background:var(--green);border-radius:4px;display:flex;align-items:center;justify-content:center;color:var(--white);font-size:44px;font-weight:700;padding-top:60px}

/* footer */
.footer-nav{left:0;top:2770px;width:1200px;display:flex;justify-content:center;gap:40px;font-size:16px;color:#333;padding-left:40px}
.social{left:0;top:2831px;width:1200px;display:flex;justify-content:center;gap:14px;padding-left:14px}
.social span{width:29px;height:29px;border-radius:3px}
.footer-bar{left:0;top:2876px;width:1200px;height:46px;background:var(--footer);color:#bbb;font-size:12px;display:flex;align-items:center;justify-content:center}
</style>
</head>
<body>

<header class="site-header abs">
  <div class="brand abs"><span class="brand-dot"></span><span class="brand-name">Trevani</span></div>
  <nav class="main-nav abs"><span>Home</span><span>About</span><span>Work With Me</span><span>Press</span><span>Events</span><span>Contact</span><span>Shop</span></nav>
</header>

<section class="hero abs" role="img" aria-label="Photo of a cheering crowd of smiling people pointing toward the viewer"></section>
<h1 class="hero-title abs">International goal achievement coach</h1>
<p class="hero-offer abs">Get FREE Tips for Sign Up</p>
<div class="field field-name abs">First name</div>
<div class="field field-mail abs">Email</div>
<div class="get-it abs">get it</div>
<div class="slider-dots abs"><span></span><span></span><span></span><span class="off"></span></div>

<!-- post 1 -->
<h2 class="post-title abs" style="left:109px;top:639px;width:577px;height:97px">I help people who are stuck, people who have<br>a big dream, but don't know how to get there.</h2>
<div class="photo abs" style="left:111px;top:736px;width:575px;height:320px;background:linear-gradient(180deg,#2a2e2a 0%,#3a4a30 60%,#2e5a26 100%)" role="img" aria-label="Photo of a footballer running on a pitch"></div>
<span class="comments abs" style="left:103px;top:736px">60 comments</span>
<div class="body-copy abs" style="left:109px;top:1068px;width:580px">
  <p>Duis aute irure dolor in reprehenderit in voluptate velit esse cillum dolore eu fugiat nulla pariatur. Excepteur sint occaecat cupidatat non proident, sunt in culpa qui officia deserunt mollit anim id est laborum</p>
  <p>Nemo enim ipsam voluptatem quia voluptas sit aspernatur aut odit aut fugit, sed quia consequuntur magni dolores eos qui ratione voluptatem sequi nesciunt. Neque porro quisquam est, qui dolorem ipsum quia dolor sit amet, consectetur, adipisci velit, sed quia non numquam eius modi tempora</p>
</div>
<p class="share-label abs" style="left:113px;top:1221px">Share this</p>
<div class="share-row abs" style="left:111px;top:1256px">
  <span class="share-btn">Friendbook <span class="count">9k+</span></span>
  <span class="share-btn">Chirper <span class="count">33</span></span>
  <span class="share-btn">Linkwork</span>
  <span class="share-btn">Pinboard</span>
</div>

<!-- post 2 -->
<h2 class="post-title abs" style="left:101px;top:1301px;width:585px;height:98px">I help them to break their dreams down into<br>small, manageable steps...</h2>
<div class="photo abs" style="left:101px;top:1399px;width:585px;height:319px;background:linear-gradient(160deg,#5a626c 0%,#3a424c 55%,#2a3038 100%)" role="img" aria-label="Photo of an athlete leaping over a hurdle"></div>
<span class="comments abs" style="left:95px;top:1399px">60 comments</span>
<div class="body-copy abs" style="left:107px;top:1729px;width:582px">
  <p>Duis aute irure dolor in reprehenderit in voluptate velit esse cillum dolore eu fugiat nulla pariatur. Excepteur sint occaecat cupidatat non proident, sunt in culpa qui officia deserunt mollit anim id est laborum</p>
  <p>Nemo enim ipsam voluptatem quia voluptas sit aspernatur aut odit aut fugit, sed quia consequuntur magni dolores eos qui ratione voluptatem sequi nesciunt. Neque porro quisquam est, qui dolorem ipsum quia dolor sit amet, consectetur, adipisci velit, sed quia non numquam eius modi tempora</p>
</div>
<p class="share-label abs" style="left:107px;top:1890px">Share this</p>
<div class="share-row abs" style="left:103px;top:1925px">
  <span class="share-btn">Friendbook <span class="count">1k+</span></span>
  <span class="share-btn">Chirper <span class="count">33</span></span>
  <span class="share-btn">Linkwork</span>
  <span class="share-btn">Pinboard</span>
</div>

<!-- post 3 -->
<h2 class="post-title abs" style="left:107px;top:1971px;width:583px;height:98px">I'm the "kick in the shin" to get them<br>moving and thriving!</h2>
<span class="comments abs" style="left:107px;top:2079px">60 comments</span>
<div class="body-copy abs" style="left:107px;top:2129px;width:582px">
  <p>Duis aute irure dolor in reprehenderit in voluptate velit esse cillum dolore eu fugiat nulla pariatur. Excepteur sint occaecat cupidatat non proident, sunt in culpa qui officia deserunt mollit anim id est laborum</p>
  <p>Nemo enim ipsam voluptatem quia voluptas sit aspernatur aut odit aut fugit, sed quia consequuntur magni dolores eos qui ratione voluptatem sequi nesciunt. Neque porro quisquam est, qui dolorem ipsum quia dolor sit amet, consectetur, adipisci velit, sed quia non numquam eius modi tempora</p>
</div>

<!-- newsletter articles -->
<h3 class="article-title abs" style="left:103px;top:2338px;width:560px">To take a trivial example, which of us ever undertakes</h3>
<p class="article-date abs" style="left:107px;top:2410px">October 12 , 2014</p>
<div class="body-copy abs" style="left:107px;top:2437px;width:582px"><p>Duis aute irure dolor in reprehenderit in voluptate velit esse cillum dolore eu fugiat nulla pariatur. Excepteur sint occaecat cupidatat non proident, sunt in culpa qui officia deserunt mollit anim id est laborum</p></div>

<h3 class="article-title abs" style="left:103px;top:2530px;width:560px">How to handle success</h3>
<p class="article-date abs" style="left:107px;top:2576px">October 12 , 2014</p>
<div class="body-copy abs" style="left:107px;top:2602px;width:582px"><p>Duis aute irure dolor in reprehenderit in voluptate velit esse cillum dolore eu fugiat nulla pariatur. Excepteur sint occaecat cupidatat non proident, sunt in culpa qui officia deserunt mollit anim id est laborum</p></div>

<div class="older abs">
  <svg width="14" height="10" viewBox="0 0 14 10"><path d="M5 1 1 5l4 4M1 5h13" fill="none" stroke="#333" stroke-width="1.6"/></svg>
  Older Posts
</div>

<!-- sidebar -->
<aside class="hot-events abs">
  <div class="widget-head">Hot Events</div>
  <div class="hot-photo" role="img" aria-label="Photo of a footballer kicking a ball mid-air">
    <div class="hot-caption"><small>Click here to Watch</small><strong>Hot Events</strong></div>
  </div>
</aside>
<p class="side-label abs" style="left:743px;top:893px">Testimonial</p>
<div class="testimonial abs">
  Duis aute irure dolor in reprehenderit in voluptate velit esse cillum dolore eu fugiat nulla pariatur. Excepteur sint occaecat cupidatat non proident, sunt in culpa qui officia deserunt mollit anim id est laborum
  <div class="testimonial-date">12-10-2014</div>
</div>
<div class="testimonial-tail abs"></div>
<p class="side-label abs" style="left:743px;top:1090px">Resources</p>
<div class="resource r1 abs" role="img" aria-label="Banner photo of a footballer on a golden background"><h3>Lorium Ipsum</h3><p>Nemo enim • modi</p></div>
<div class="resource r2 abs" role="img" aria-label="Banner photo of a woman in warm tones"><h3>Lorium Ipsum</h3><p>Nemo enim • modi</p></div>
<div class="resource r3 abs" role="img" aria-label="Banner with a faint world map"><h3>Lorium Ipsum</h3><p>Nemo enim • modi</p></div>
<div class="music abs">Tunestream</div>

<!-- footer -->
<nav class="footer-nav abs"><span>Home</span><span>About</span><span>Work With Me</span><span>Press</span><span>Events</span><span>Contact</span><span>Shop</span></nav>
<div class="social abs">
  <span style="background:#3b5998"></span>
  <span style="background:#33aadd"></span>
  <span style="background:#2a6ebb"></span>
  <span style="background:#f28a1b"></span>
</div>
<footer class="footer-bar abs">© 2014.www.companyname.com</footer>

</body>
</html>
```